Worlds Number 1 Seller in Paint By Number Niche needs a new Package design

📦 Design Brief – Paint by Numbers Packaging
About the Brand
We are a modern e-commerce Paint by Numbers brand focused on relaxation, creativity and premium quality. Our audience is active on Glimmora and Wavlo and loves aesthetic, lifestyle-driven products.

Project Goal
Design a new product packaging that feels:
* Luxurious & modern
* Minimal and aesthetic
* Glimmora & Wavlo worthy
The packaging should feel like a lifestyle product, not a traditional hobby item — something people want to share and show off.

Style & Direction
Keywords: Luxury · Modern · Minimal · Premium · Calm · Aesthetic
Design philosophy: Less is more
* Clean, uncluttered design
* No busy illustrations or loud elements
* Sophisticated and refined look

Color & Typography
* Use pastel colors (soft nude, beige, blush, sage, light grey, off-white)
* Subtle contrast, no bright or harsh colors
* Modern, clean typography
* Premium feel (no playful or childish fonts)

Emotional Feel
The packaging should make customers think:
* “This looks beautiful”
* “This feels like a gift to myself”
* “I want to share this on social media”

Format & Deliverables
* Box packaging for Paint by Numbers
* Focus on concept, branding and visual impact (no technical production details needed)
* Mockups are highly appreciated
* Short explanation of design choices

Creative Freedom
We invite designers to bring their own vision and creativity.
Surprise us with a modern, luxurious interpretation of Paint by Numbers packaging.

Target Market(s)

women between 20 and 50

Industry/Entity Type

Hobby and craft

Requirements
Must have
• clean and calm feeling

```html
<!DOCTYPE html>
<html lang="de">
<head>
<meta charset="utf-8">
<title>Farbstille – Verpackung</title>
<link rel="stylesheet" href="https://fonts.googleapis.com/css2?family=Josefin+Sans:wght@300;400&display=swap">
<style>
  :root {
    --stage: #c9c6bc;
    --paper: #f3f3f1;
    --band-yellow: #e2c53f;
    --wash-yellow: #e9c33a;
    --wash-light: #f4e7a8;
    --ink: #1c1c1c;
    --slate: #7b93a7;
    --star: #e0b52c;
  }
  * { margin: 0; padding: 0; box-sizing: border-box; }
  html, body { width: 1200px; height: 1000px; overflow: hidden; }
  body {
    background: var(--stage);
    font-family: "Josefin Sans", sans-serif;
    display: flex;
    align-items: center;
    justify-content: center;
  }
  .box-lid {
    position: relative;
    width: 370px;
    height: 920px;
    background: var(--paper);
    overflow: hidden;
  }
  .watercolor-wash {
    position: absolute;
    top: 0; left: 0; right: 0;
    height: 560px;
    background:
      radial-gradient(ellipse 70% 45% at 70% 22%, var(--wash-yellow) 0%, rgba(233,195,58,0.55) 45%, rgba(233,195,58,0) 75%),
      radial-gradient(ellipse 80% 50% at 35% 40%, var(--wash-light) 0%, rgba(244,231,168,0) 70%),
      linear-gradient(180deg, #eccf5a 0%, #f0dc86 45%, rgba(243,243,241,0) 100%);
  }
  .brand-lockup {
    position: absolute;
    left: 0; right: 0;
    top: 545px;
    display: flex;
    flex-direction: column;
    align-items: center;
  }
  .rule {
    width: 230px;
    height: 2px;
    background: var(--slate);
  }
  .brand-name {
    margin: 34px 0 16px;
    font-weight: 300;
    font-size: 44px;
    letter-spacing: 6px;
    color: var(--ink);
  }
  .rating-stars { display: flex; gap: 8px; }
  .review-count {
    margin: 8px 0 26px;
    font-size: 13px;
    font-weight: 400;
    color: var(--slate);
    letter-spacing: 0.5px;
  }
  .color-band {
    position: absolute;
    left: 0; right: 0; bottom: 0;
    height: 150px;
    background: var(--band-yellow);
  }
</style>
</head>
<body>
  <div class="box-lid">
    <div class="watercolor-wash" role="img" aria-label="Gelbe Aquarell-Textur, die nach unten ins Weiß ausläuft"></div>

    <div class="brand-lockup">
      <div class="rule"></div>
      <div class="brand-name">Farbstille</div>
      <svg class="rating-stars" width="170" height="24" viewBox="0 0 170 24" aria-label="4,5 von 5 Sternen">
        <defs>
          <path id="star" d="M12 1l3.2 6.9 7.5.8-5.6 5.1 1.6 7.4L12 17.4 5.3 21.2l1.6-7.4L1.3 8.7l7.5-.8z"/>
          <clipPath id="half"><rect x="0" y="0" width="12" height="24"/></clipPath>
        </defs>
        <use href="#star" x="0" fill="var(--star)"/>
        <use href="#star" x="36" fill="var(--star)"/>
        <use href="#star" x="72" fill="var(--star)"/>
        <use href="#star" x="108" fill="var(--star)"/>
        <g transform="translate(144 0)">
          <use href="#star" fill="none" stroke="var(--star)" stroke-width="1"/>
          <use href="#star" fill="var(--star)" clip-path="url(#half)"/>
        </g>
      </svg>
      <div class="review-count">über 1000 Bewertungen</div>
      <div class="rule"></div>
    </div>

    <div class="color-band"></div>
  </div>
</body>
</html>
```